Harvest Gateway Fellowship Ministries needs a fresh new web design

We are an up and coming multicultural church that aims to bring people into a life changing encounter with God. We need a fresh and inviting website in order to increase our internet presence and make us easier to connect with.
Here are some of the basic requirements for the site:
• Clearly displayed address, service times, and contact info
• A staff profile page
• An area for a calendar with upcoming events and their details
• Social media buttons
• Group pages for the different ministries (youth, children’s church, men, etc…)
• An area for donations and eCommerce
• A resources page for assorted media (podcasts, sermons, videos, etc.…)
• An area for prayer requests.

```html
<!DOCTYPE html>
<html lang="en">
<head>
<meta charset="utf-8">
<title>Harvest Gateway Fellowship Ministries</title>
<link href="https://fonts.googleapis.com/css2?family=Lato:wght@400;700&family=Arimo:wght@400;700&display=swap" rel="stylesheet">
<style>
:root{
  --blue:#0b4f78;
  --blue-dark:#083f61;
  --gold:#f2d65c;
  --card:#fbefb6;
  --card-line:#e6cf83;
  --cream:#fbf4cf;
  --text:#3f3f3f;
  --muted:#666;
  --line:#ececec;
  --accent:#e8872a;
}
*{margin:0;padding:0;box-sizing:border-box}
html,body{width:832px;height:1200px;overflow:hidden;background:#fff}
body{position:relative;font-family:'Arimo',Arial,sans-serif;color:var(--text)}
.abs{position:absolute}
.sky-header{left:0;top:0;width:832px;height:121px;background:linear-gradient(180deg,#cdb48a 0%,#e9dcc1 55%,#fbf6ec 100%)}
.brand{left:0;top:30px;width:832px;text-align:center}
.brand-mark{width:34px;height:34px;border-radius:50%;background:var(--gold);margin:0 auto 6px}
.brand-name{font-family:'Lato',sans-serif;font-size:10px;font-weight:700;color:var(--blue-dark)}
.main-nav{left:0;top:121px;width:832px;height:41px;background:var(--blue)}
.main-nav a{position:absolute;top:0;height:41px;line-height:41px;color:#fff;text-decoration:none;font-size:10.5px;transform:translateX(-50%)}
.nav-sep{position:absolute;top:0;width:1px;height:41px;background:var(--blue-dark)}
.hero{left:125px;top:179px;width:583px;height:274px;background:radial-gradient(ellipse at 72% 25%,#f6e8c2 0%,#c9a66c 40%,#7f6440 100%)}
.hero-arrow{position:absolute;top:120px;width:33px;height:33px;border:2px solid rgba(255,255,255,.7);border-radius:50%}
.hero-quote{position:absolute;left:0;width:583px;top:218px;text-align:center;font-family:'Lato',sans-serif;font-weight:700;font-size:21px;color:#fff}
.welcome-title{left:0;width:832px;top:462px;text-align:center;font-family:'Lato',sans-serif;font-size:16px;color:#222}
.welcome-title b{color:var(--blue)}
.welcome-text{left:150px;width:532px;top:491px;text-align:center;font-size:7.4px;line-height:13px;color:#444}
.feature{top:545px;width:183px;height:163px;background:var(--card);border:1px solid var(--card-line)}
.feature-inner{position:absolute;inset:12px;border:1px solid var(--card-line);text-align:center;font-family:'Lato',sans-serif;color:#555}
.feature h3{font-weight:400;font-size:15px;margin-top:12px}
.verse-ref{font-size:11px;margin-top:8px}
.btn{display:inline-block;background:var(--gold);color:#6a5418;font-size:10px;padding:5px 11px;border-radius:2px}
.section-title{top:727px;font-family:'Lato',sans-serif;font-size:15px;color:#444}
.staff-card{left:125px;width:281px;height:112px;border:1px solid var(--line);background:#fdfdfd}
.staff-photo{position:absolute;left:0;top:0;width:102px;height:110px;background:linear-gradient(180deg,#e4e9f2,#b9c2d2)}
.staff-body{position:absolute;left:118px;top:8px;width:155px;font-family:'Lato',sans-serif}
.staff-body h4{font-weight:400;font-size:11px;color:#444;margin-bottom:6px}
.staff-body p{font-size:7.6px;line-height:15.5px;color:#555}
.read-more{font-size:8px;color:#444;margin-top:4px}
.read-more span{color:var(--accent)}
.event-card{left:426px;width:282px;height:75px;border:1px solid var(--line)}
.event-date{position:absolute;left:0;top:0;width:46px;height:73px;border-right:1px solid var(--line);text-align:center;font-family:'Lato',sans-serif}
.event-date svg{margin-top:10px}
.event-month{font-size:11px;color:#555;margin-top:2px}
.event-body{position:absolute;left:53px;top:8px;width:222px;font-family:'Lato',sans-serif}
.event-body h5{font-weight:400;font-size:9.4px;line-height:15.5px;color:#555}
.event-meta{font-size:6.8px;color:#555;margin-top:5px;line-height:13.5px}
.event-meta i{display:inline-block;width:5px;height:5px;border:1px solid #aaa;margin:0 6px 0 1px;vertical-align:middle}
.site-footer{left:0;top:1011px;width:832px;height:146px;background:var(--cream)}
.footer-head{position:absolute;top:15px;font-size:8px;color:#777;letter-spacing:.3px}
.prayer-list{position:absolute;left:125px;top:34px;width:215px;font-size:7.4px;line-height:14px;color:#666}
.prayer-list p{margin-bottom:4px}
.social{position:absolute;width:20px;height:20px;border-radius:50%;border:1px solid #e2d9ae}
.contact-row{position:absolute;left:576px;font-size:7px;line-height:13px;color:#777}
.contact-icon{position:absolute;left:-18px;top:-2px;width:20px;height:20px;border-radius:50%;border:1px solid #e2d9ae}
.bottom-bar{left:0;top:1157px;width:832px;height:43px;border-top:1px solid #eee}
.copyright{position:absolute;left:0;width:808px;top:18px;text-align:center;font-size:7.4px;color:#777}
</style>
</head>
<body>

<header>
  <div class="abs sky-header" role="img" aria-label="Soft golden sky with clouds and two doves"></div>
  <div class="abs brand">
    <div class="brand-mark"></div>
    <div class="brand-name">Harvest Gateway Fellowship Ministries</div>
  </div>
  <nav class="abs main-nav">
    <a href="#" style="left:164px">Home</a>
    <span class="nav-sep" style="left:202px"></span>
    <a href="#" style="left:246px">About Us</a>
    <span class="nav-sep" style="left:290px"></span>
    <a href="#" style="left:330px">Events</a>
    <span class="nav-sep" style="left:371px"></span>
    <a href="#" style="left:428px">Prayer Request</a>
    <span class="nav-sep" style="left:488px"></span>
    <a href="#" style="left:526px">Donate</a>
    <span class="nav-sep" style="left:566px"></span>
    <a href="#" style="left:615px">Contact Us</a>
  </nav>
</header>

<section class="abs hero" role="img" aria-label="Wooden cross against a glowing cloudy sky">
  <span class="hero-arrow" style="left:32px"><svg width="29" height="29"><path d="M17 8 L11 14.5 L17 21" stroke="#fff" stroke-width="1.6" fill="none"/></svg></span>
  <span class="hero-arrow" style="left:518px"><svg width="29" height="29"><path d="M12 8 L18 14.5 L12 21" stroke="#fff" stroke-width="1.6" fill="none"/></svg></span>
  <p class="hero-quote">"No limits, No Boundaries, but increase in Jesus name"</p>
</section>

<h1 class="abs welcome-title" style="font-weight:400">Welcome To <b>HGFM</b></h1>
<p class="abs welcome-text">Welcome to Harvest Gateway Fellowship Ministries, a place where we can come together and fellowship. HGFM is located in Brookdale Heights and we would love to have you worship with us. We believe God is doing something extraordinary through our church and would like for you to be a part. Please prayerfully consider our church as a place you would like to worship and fellowship with us as we continue to grow.</p>

<section class="abs feature" style="left:125px">
  <div class="feature-inner">
    <h3>Service Times</h3>
    <p style="font-size:11px;margin-top:10px">Random Bible Verse</p>
    <p style="font-size:9.6px;line-height:15.5px;margin:6px 6px 0">For what shall it profit a man if he shall gain the whole world and lose his own soul?</p>
    <p class="verse-ref">Mark 8:36</p>
  </div>
</section>
<section class="abs feature" style="left:324px">
  <div class="feature-inner">
    <h3 style="margin-top:10px">Prayer Requests</h3>
    <div style="width:62px;height:62px;border-radius:50%;border:1px solid var(--card-line);margin:8px auto 10px;display:flex;align-items:center;justify-content:center">
      <div role="img" aria-label="Open prayer book" style="width:30px;height:30px;background:var(--gold);border-radius:3px"></div>
    </div>
    <span class="btn">Read More</span>
  </div>
</section>
<section class="abs feature" style="left:525px">
  <div class="feature-inner">
    <div role="img" aria-label="Hand dropping a coin" style="position:absolute;left:48px;top:0;width:96px;height:96px;background:linear-gradient(160deg,#f6e2cf,#e6c4a6)"></div>
    <div style="position:absolute;left:12px;top:62px;width:48px;height:48px;border-radius:50%;background:#e9c83e"></div>
    <h3 style="position:absolute;left:0;right:0;top:112px;margin:0">Donations</h3>
  </div>
</section>

<h2 class="abs section-title" style="left:125px;font-weight:400">Our Staff</h2>
<h2 class="abs section-title" style="left:426px;font-weight:400">Upcomming Events</h2>

<article class="abs staff-card" style="top:755px">
  <div class="staff-photo" role="img" aria-label="Portrait of the pastor holding a Bible"></div>
  <div class="staff-body">
    <h4>Pastor Daniel Okafor</h4>
    <p>Daniel Okafor is a native of the Caribbean island of Jamaica and strongly believes that God's calling on his life is to teach and preach the Gospel to everyone</p>
    <p class="read-more">Read More <span>›</span></p>
  </div>
</article>
<article class="abs staff-card" style="top:881px">
  <div class="staff-photo" role="img" aria-label="Portrait of the minister holding a Bible"></div>
  <div class="staff-body">
    <h4>Minister Grace Okafor</h4>
    <p>Daniel Okafor is a native of the Caribbean island of Jamaica and strongly believes that God's calling on his life is to teach and preach the Gospel to everyone</p>
    <p class="read-more">Read More <span>›</span></p>
  </div>
</article>

<article class="abs event-card" style="top:755px">
  <div class="event-date"><svg width="26" height="26"><rect x="1" y="2" width="24" height="22" fill="#fff" stroke="#999"/><rect x="1" y="2" width="24" height="5" fill="#333"/><text x="13" y="20" font-size="11" text-anchor="middle" fill="#555" font-family="Lato">01</text></svg><p class="event-month">Jul</p></div>
  <div class="event-body"><h5>Aenean commodo dolor at sapien luc tus non venena Aenean commodo dolor</h5><p class="event-meta"><i></i>12:00 PM - 1:00 PM<br><i style="border-radius:50%"></i>Location: Lorum ipsum Church</p></div>
</article>
<article class="abs event-card" style="top:837px">
  <div class="event-date"><svg width="26" height="26"><rect x="1" y="2" width="24" height="22" fill="#fff" stroke="#999"/><rect x="1" y="2" width="24" height="5" fill="#333"/><text x="13" y="20" font-size="11" text-anchor="middle" fill="#555" font-family="Lato">02</text></svg><p class="event-month">Jul</p></div>
  <div class="event-body"><h5>Aenean commodo dolor at sapien luc tus non venena Aenean commodo dolor</h5><p class="event-meta"><i></i>12:00 PM - 1:00 PM<br><i style="border-radius:50%"></i>Location: Lorum ipsum Church</p></div>
</article>
<article class="abs event-card" style="top:918px">
  <div class="event-date"><svg width="26" height="26"><rect x="1" y="2" width="24" height="22" fill="#fff" stroke="#999"/><rect x="1" y="2" width="24" height="5" fill="#333"/><text x="13" y="20" font-size="11" text-anchor="middle" fill="#555" font-family="Lato">03</text></svg><p class="event-month">Jul</p></div>
  <div class="event-body"><h5>Aenean commodo dolor at sapien luc tus non venena Aenean commodo dolor</h5><p class="event-meta"><i></i>12:00 PM - 1:00 PM<br><i style="border-radius:50%"></i>Location: Lorum ipsum Church</p></div>
</article>

<footer class="abs site-footer">
  <h6 class="footer-head" style="left:124px;font-weight:400">PRAYER LISTING</h6>
  <div class="prayer-list">
    <p>i feel like giving up please pray for me and other issues i'm going through in my life. Marcus</p>
    <p>Prayer Requested By: Marcus, 03-28-2012 - 11:08:41 AM</p>
    <p>"I am a asking you to pray for God's direction in my life. At this time, I am faced with uncerta ..."</p>
    <p>Prayer Requested By: Marcus, 03-28-2012 - 11:08:41 AM</p>
  </div>
  <h6 class="footer-head" style="left:403px;font-weight:400">FOLLOW US!</h6>
  <span class="social" style="left:401px;top:39px"></span>
  <span class="social" style="left:434px;top:39px"></span>
  <span class="social" style="left:467px;top:39px"></span>
  <span class="social" style="left:499px;top:39px"></span>
  <span class="social" style="left:401px;top:68px"></span>
  <span class="social" style="left:434px;top:68px"></span>
  <h6 class="footer-head" style="left:581px;font-weight:400">GET IN TOUCH</h6>
  <div class="contact-row" style="top:39px;left:604px"><span class="contact-icon" style="left:-28px;top:2px"><svg width="18" height="18"><path d="M9 3a4 4 0 0 1 4 4c0 3-4 8-4 8s-4-5-4-8a4 4 0 0 1 4-4z" fill="#333"/><circle cx="9" cy="7" r="1.5" fill="#fff"/></svg></span>Christian&nbsp; 412 Cedar Lane,<br>Millbrook, MB4 2KT.</div>
  <div class="contact-row" style="top:77px;left:605px"><span class="contact-icon" style="left:-29px;top:-4px"><svg width="18" height="18"><rect x="6" y="3" width="7" height="12" rx="1" fill="none" stroke="#333" stroke-width="1.4"/></svg></span>Phone: 555.010.4821</div>
  <div class="contact-row" style="top:109px;left:605px"><span class="contact-icon" style="left:-29px;top:-4px"><svg width="18" height="18"><rect x="4" y="5" width="11" height="8" fill="#333"/><path d="M4 5 L9.5 10 L15 5" stroke="#fff" fill="none"/></svg></span>Email: info@harvestgateway.org</div>
</footer>

<div class="abs bottom-bar"><p class="copyright">©2014 2014&nbsp; HGFM, All Rights Reserved.</p></div>

</body>
</html>
```